Business Card for a Creative Technology based HR services company

Our company name is Lumo8, and we build large communities of HR (human resource) and finance personnels through our mobile platform, and we conduct lots of on-line and off-line activities to get everyone constantly connected. Behind all these, we will also provide on-site HR and finance contractors to our clients, plus a host of other HR-related services. No process in our company takes more than 5-steps.
Our company slogan: Touching Your Future
Target Market(s)
All human resource (HR) and finance personnels, from new entrants to highly experienced senior professionals.
Industry/Entity Type
Finance
Colors
Designer to choose colors to be used in the design.
Look and feel
Each slider illustrates characteristics of the customer's brand and the style your logo design should communicate.

```html
<!DOCTYPE html>
<html lang="en">
<head>
<meta charset="utf-8">
<title>Lumo8 Business Card</title>
<link rel="stylesheet" href="https://fonts.googleapis.com/css2?family=Exo+2:wght@400;600;800&family=Oswald:wght@500&display=swap">
<style>
  :root {
    --navy: #13305e;
    --red: #ee2329;
    --red-dark: #b8161c;
    --grey: #c9c9c9;
    --white: #ffffff;
    --ink: #1c2233;
    --backdrop: #e6e7ea;
  }
  * { margin: 0; padding: 0; box-sizing: border-box; }
  html, body { width: 1200px; height: 903px; overflow: hidden; }
  body {
    background: var(--backdrop);
    font-family: "Exo 2", sans-serif;
    position: relative;
  }
  .card {
    position: absolute;
    width: 700px;
    height: 400px;
    background: var(--white);
    overflow: hidden;
    box-shadow: 0 10px 28px rgba(0,0,0,.25);
  }
  /* Back side */
  .card-back { left: 60px; top: 50px; }
  .card-back .band { position: absolute; left: 0; width: 100%; }
  .band-top { top: 0; height: 80px; background: var(--navy); }
  .band-top-rule { top: 80px; height: 26px; background: var(--grey); }
  .band-bottom-rule { top: 294px; height: 26px; background: var(--grey); }
  .band-bottom { top: 320px; height: 80px; background: var(--navy); }
  .brand {
    position: absolute;
    display: flex;
    align-items: center;
    gap: 10px;
    font-weight: 800;
    color: var(--navy);
    letter-spacing: -1px;
  }
  .brand-dot { border-radius: 50%; background: var(--red); }
  .card-back .brand { left: 50%; top: 200px; transform: translate(-50%, -50%); font-size: 76px; }
  .card-back .brand-dot { width: 46px; height: 46px; }

  /* Front side */
  .card-front { left: 440px; top: 460px; }
  .front-top-bar { position: absolute; left: 0; top: 0; width: 100%; height: 22px; background: var(--red); }
  .address {
    position: absolute; right: 36px; top: 46px;
    text-align: right; font-size: 19px; line-height: 1.4; color: var(--ink); font-weight: 600;
  }
  .front-rule { position: absolute; left: 0; top: 122px; width: 100%; height: 12px; background: var(--red); }
  .card-front .brand { left: 40px; top: 176px; font-size: 58px; }
  .card-front .brand-dot { width: 36px; height: 36px; }
  .name-block {
    position: absolute; left: 0; top: 262px; width: 400px; height: 138px;
    background: var(--navy); color: var(--white); padding: 28px 0 0 40px;
  }
  .person-name { font-family: "Oswald", sans-serif; font-size: 38px; letter-spacing: 2px; line-height: 1; }
  .person-role { font-size: 15px; letter-spacing: 3px; margin-top: 6px; }
  .contact-block {
    position: absolute; left: 400px; top: 134px; width: 300px; height: 240px; background: var(--red);
  }
  .contact-panel {
    position: absolute; left: 18px; top: 22px; width: 264px; height: 196px;
    background: linear-gradient(135deg, #d51f25, var(--red-dark));
    padding: 22px 16px 0 0;
  }
  .contact-list { list-style: none; }
  .contact-list li {
    display: flex; justify-content: flex-end; align-items: center; gap: 10px;
    color: var(--white); font-size: 14px; height: 38px;
  }
  .contact-icon { width: 20px; height: 20px; background: var(--white); border-radius: 3px; flex: none; }
</style>
</head>
<body>
  <section class="card card-back">
    <div class="band band-top"></div>
    <div class="band band-top-rule"></div>
    <div class="brand"><span class="brand-name">Lumo8</span><span class="brand-dot"></span></div>
    <div class="band band-bottom-rule"></div>
    <div class="band band-bottom"></div>
  </section>

  <section class="card card-front">
    <div class="front-top-bar"></div>
    <p class="address">42 Harbor Lane Road,<br>5th Avenue Block w.</p>
    <div class="front-rule"></div>
    <div class="brand"><span class="brand-name">Lumo8</span><span class="brand-dot"></span></div>
    <div class="name-block">
      <p class="person-name">DANIEL REYES</p>
      <p class="person-role">GENERAL MANAGER</p>
    </div>
    <div class="contact-block">
      <div class="contact-panel">
        <ul class="contact-list">
          <li>014 552 7310
            <svg class="contact-icon" viewBox="0 0 20 20"><rect width="20" height="20" rx="3" fill="#fff"/><path d="M6 4l2.5 3-1.3 1.5a8 8 0 004.3 4.3L13 11.5 16 14l-1.5 2C9 16 4 11 4 5.5z" fill="#b8161c"/></svg></li>
          <li>014 552 7311
            <svg class="contact-icon" viewBox="0 0 20 20"><rect width="20" height="20" rx="3" fill="#fff"/><rect x="5" y="6" width="10" height="9" fill="#b8161c"/><rect x="7" y="3" width="6" height="4" fill="#b8161c"/></svg></li>
          <li>hello@lumo8mail.com
            <svg class="contact-icon" viewBox="0 0 20 20"><rect width="20" height="20" rx="3" fill="#fff"/><rect x="4" y="6" width="12" height="8" fill="#b8161c"/><path d="M4 6l6 5 6-5" stroke="#fff" stroke-width="1.2" fill="none"/></svg></li>
          <li>www.lumo8hr.com
            <svg class="contact-icon" viewBox="0 0 20 20"><rect width="20" height="20" rx="3" fill="#fff"/><circle cx="10" cy="10" r="5.5" fill="none" stroke="#b8161c" stroke-width="1.5"/><path d="M4.5 10h11M10 4.5v11" stroke="#b8161c" stroke-width="1.2"/></svg></li>
        </ul>
      </div>
    </div>
  </section>
</body>
</html>
```